BRN website video quote promotion tiles

We are promoting vehicle leasing by video, which contains several quotation examples imported from the video. We must re-vamp the quotation tiles, contact boxes, and contact form. The first tile is generated from the video, so this must be a separate project. We are looking for a welcoming, professional flow and leave color choices to design with an emphasis on communication prompts, and additional prompts in the design would be welcome.

Target Market(s)

Any Customer interaction from the tile quotes, contact, call, message,

Industry/Entity Type

vehicle leasing

Coding

Coded - Design and coding required

Number of Pages Required

1 page

Colors

Designer to choose colors to be used in the design.

Requirements
Must have
• emphasis on point of contact and visual impact on quote tile excluding main one
Should not have
• changes to the quote structure as these imported from video pricing no changes to main image as this template which can addressed as separate project

```html
<!DOCTYPE html>
<html lang="en">
<head>
<meta charset="utf-8">
<title>BRN Contract Hire Quote Tiles</title>
<link href="https://fonts.googleapis.com/css2?family=Poppins:wght@400;500;600;700&family=Oswald:wght@500;600&display=swap" rel="stylesheet">
<style>
:root{
  --page:#c0d66d;
  --white:#ffffff;
  --blue:#0d4fe0;
  --purple:#7a3fc4;
  --red:#d23434;
  --orange:#f9a11b;
  --chat:#44e020;
  --ink:#333333;
  --green-text:#2a9a2a;
  --alert:#ee1111;
  --submit:#9aba1e;
  --line:#8a8a8a;
}
*{box-sizing:border-box;margin:0;padding:0}
html,body{width:1200px;height:847px;overflow:hidden;background:var(--page)}
body{font-family:'Poppins',sans-serif}
.stage{position:relative;width:1700px;height:1200px;transform:scale(.70588);transform-origin:0 0}
.panel{position:absolute;left:50px;width:1600px;background:var(--white);overflow:hidden}
.panel--tiles{top:22px;height:396px}
.panel--form{top:461px;height:739px}
.abs{position:absolute}
.price{font-family:'Oswald',sans-serif;font-weight:600;color:var(--white)}
.btn{position:absolute;height:55px;border-radius:28px;display:flex;align-items:center;justify-content:center;gap:10px;color:var(--white);font-weight:600;font-size:16px;letter-spacing:.5px;white-space:nowrap}
.btn svg{width:14px;height:14px}
.btn--call-dark{background:#000}
.btn--call{background:linear-gradient(90deg,#3f63d4,#8a3fc8)}
.btn--chat{background:var(--chat);font-size:17px}
.btn--chat .dot{width:14px;height:14px;border-radius:50%;background:var(--white)}
/* tile 1 */
.tile-one{left:29px;top:52px;width:492px;height:278px;border-radius:60px 0 60px 0;background:linear-gradient(120deg,#a9bde8,#c8a6e0)}
.tile-one .label{left:0;top:40px;width:211px;height:61px;background:var(--blue);border-radius:0 30px 30px 0;color:var(--white);font-weight:700;font-size:20px;display:flex;align-items:center;padding-left:20px;white-space:nowrap}
.tile-one .badge{left:351px;top:12px;width:118px;height:118px;border-radius:50%;border:3px solid var(--white);background:linear-gradient(135deg,#2a5fd0,#7b3fc0);display:flex;flex-direction:column;align-items:center;justify-content:center}
.tile-one .badge .price{font-size:30px;line-height:1}
.vat{color:var(--orange);font-weight:700;font-size:12px;letter-spacing:.5px}
.tile-one .terms{left:20px;top:123px;color:var(--white);font-size:19px;font-weight:500;white-space:nowrap}
.tile-one .state{left:20px;top:152px;color:var(--alert);font-size:18px;font-weight:500}
/* tile 2 */
.tile-two{left:555px;top:52px;width:492px;height:278px;background:#efefef;box-shadow:0 2px 8px rgba(0,0,0,.25)}
.ribbon{left:540px;top:74px;width:521px;height:59px}
.ribbon .title{left:30px;top:0;height:59px;line-height:59px;color:var(--white);font-weight:700;font-size:24px;white-space:nowrap}
.ribbon .price{left:329px;top:4px;font-size:34px}
.ribbon .vat-dark{left:440px;top:22px;font-size:11px;font-weight:700;color:#222;white-space:nowrap}
.center-text{left:0;width:100%;text-align:center;color:#222}
.tile-two .terms{top:110px;font-size:26px;font-weight:500}
.green-note{color:var(--green-text);font-size:16px}
.tile-two .green-note{top:150px}
/* tile 3 */
.tile-three{left:1081px;top:52px;width:490px;height:278px;border:2px solid #6a4fc8;border-radius:40px;background:var(--white);overflow:hidden}
.tab-red{left:33px;top:10px;width:243px;height:65px;background:var(--red);border-radius:18px 18px 0 0;color:var(--white);font-weight:700;font-size:24px;text-align:center;line-height:62px;white-space:nowrap}
.tab-purple{left:295px;top:10px;width:162px;height:60px;background:var(--purple);border-radius:18px 18px 0 0;text-align:center}
.tab-purple .price{font-size:33px;line-height:48px}
.tile-three .card{left:2px;top:64px;width:482px;height:214px;border-radius:50px 50px 0 0;background:linear-gradient(180deg,#e6e6e6,#f8f8f8)}
.vat-pill{left:333px;top:55px;width:86px;height:26px;border-radius:13px;background:var(--orange);color:#222;font-size:11px;font-weight:700;text-align:center;line-height:26px}
.tile-three .terms{top:30px;font-size:28px;font-weight:500;line-height:1.12}
.tile-three .green-note{top:96px}
/* overlay and form */
.dim{position:absolute;inset:0;background:rgba(0,0,0,.6)}
.modal{left:158px;top:153px;width:1284px;height:552px;background:var(--white);border-radius:60px 0 60px 0}
.modal-head{left:86px;top:20px;width:1111px;height:58px;border-radius:30px;background:var(--ink);color:var(--white);font-size:28px;font-weight:500;text-align:center;line-height:58px;letter-spacing:.5px}
.modal-head::after{content:"";position:absolute;left:545px;bottom:-19px;border:11px solid transparent;border-top:9px solid var(--ink);border-left-width:11px}
.close{left:1218px;top:26px;width:48px;height:48px;border-radius:50%;border:1.5px solid #999;display:flex;align-items:center;justify-content:center}
.field{position:absolute;border:1px solid var(--line);border-radius:30px;display:flex;align-items:center;gap:10px;padding-left:22px;font-size:15px;color:#222}
.field svg{width:15px;height:15px}
.field--msg{align-items:flex-start;padding-top:22px}
.submit{left:515px;top:456px;width:252px;height:58px;border-radius:30px;background:var(--submit);color:var(--white);font-weight:700;font-size:26px;text-align:center;line-height:58px;letter-spacing:.5px}
.count{right:12px;bottom:22px;color:var(--white);font-size:24px}
</style>
</head>
<body>
<div class="stage">

  <section class="panel panel--tiles">
    <div class="abs tile-one">
      <div class="abs label">CONTRACT HIRE</div>
      <div class="abs badge"><span class="price">£247.33</span><span class="vat">PLUS VAT</span></div>
      <p class="abs terms">3 years, 9+35, 10K miles annually</p>
      <p class="abs state">Not Maintained</p>
      <a class="btn btn--call-dark" style="left:21px;top:197px;width:177px"><svg viewBox="0 0 16 16"><path d="M4 1l2 3-1.5 1.5a9 9 0 0 0 6 6L12 10l3 2-1 3c-7 0-13-6-13-13z" fill="#fff"/></svg>CONTACT US</a>
      <a class="btn btn--chat" style="left:206px;top:197px;width:100px"><span class="dot"></span>Chat</a>
    </div>

    <div class="abs tile-two">
      <p class="abs center-text terms">3 years, 9+35, 10K miles annually</p>
      <p class="abs center-text green-note">Complete Servicing and Maintenance included</p>
      <a class="btn btn--call" style="left:63px;top:197px;width:177px"><svg viewBox="0 0 16 16"><path d="M4 1l2 3-1.5 1.5a9 9 0 0 0 6 6L12 10l3 2-1 3c-7 0-13-6-13-13z" fill="#fff"/></svg>CONTACT US</a>
      <a class="btn btn--chat" style="left:253px;top:197px;width:177px"><span class="dot"></span>Chatline</a>
    </div>
    <div class="abs ribbon">
      <svg class="abs" width="521" height="71" viewBox="0 0 521 71">
        <polygon points="0,12 15,0 15,71 0,59" fill="#3a1a12"/>
        <polygon points="521,12 506,0 506,71 521,59" fill="#3a1a12"/>
        <polygon points="0,0 323,0 296,59 0,59" fill="#d23434"/>
        <polygon points="323,0 521,0 521,59 296,59" fill="#f9a11b"/>
      </svg>
      <span class="abs title">CONTRACT HIRE</span>
      <span class="abs price">£247.33</span>
      <span class="abs vat-dark">PLUS VAT</span>
    </div>

    <div class="abs tile-three">
      <div class="abs tab-red">CONTRACT HIRE</div>
      <div class="abs tab-purple"><span class="price">£247.33</span></div>
      <div class="abs card">
        <p class="abs center-text terms">3 years, 9+35, 10K<br>miles annually</p>
        <p class="abs center-text green-note">Complete Servicing and Maintenance included</p>
        <a class="btn btn--call" style="left:58px;top:139px;width:175px"><svg viewBox="0 0 16 16"><path d="M4 1l2 3-1.5 1.5a9 9 0 0 0 6 6L12 10l3 2-1 3c-7 0-13-6-13-13z" fill="#fff"/></svg>CONTACT US</a>
        <a class="btn btn--chat" style="left:248px;top:139px;width:176px"><span class="dot"></span>Chatline</a>
      </div>
      <div class="abs vat-pill">PLUS VAT</div>
    </div>
  </section>

  <section class="panel panel--form">
    <div class="abs tile-one">
      <div class="abs label">CONTRACT HIRE</div>
      <div class="abs badge"><span class="price">£247.33</span><span class="vat">PLUS VAT</span></div>
      <p class="abs terms">3 years, 9+35, 10K miles annually</p>
      <p class="abs state">Not Maintained</p>
      <a class="btn btn--call-dark" style="left:21px;top:197px;width:177px">CONTACT US</a>
    </div>
    <div class="abs tile-two"></div>
    <div class="abs ribbon">
      <svg class="abs" width="521" height="71" viewBox="0 0 521 71">
        <polygon points="0,12 15,0 15,71 0,59" fill="#3a1a12"/>
        <polygon points="521,12 506,0 506,71 521,59" fill="#3a1a12"/>
        <polygon points="0,0 323,0 296,59 0,59" fill="#d23434"/>
        <polygon points="323,0 521,0 521,59 296,59" fill="#f9a11b"/>
      </svg>
      <span class="abs title">CONTRACT HIRE</span>
      <span class="abs price">£247.33</span>
      <span class="abs vat-dark">PLUS VAT</span>
    </div>
    <div class="abs tile-three">
      <div class="abs tab-red">CONTRACT HIRE</div>
      <div class="abs tab-purple"><span class="price">£247.33</span></div>
      <div class="abs card">
        <p class="abs center-text terms">3 years, 9+35, 10K<br>miles annually</p>
        <p class="abs center-text green-note">Complete Servicing and Maintenance included</p>
        <a class="btn btn--chat" style="left:248px;top:139px;width:176px"></a>
      </div>
      <div class="abs vat-pill">PLUS VAT</div>
    </div>

    <div class="dim"></div>

    <form class="abs modal">
      <div class="abs modal-head">Please submit your contact details</div>
      <div class="abs close"><svg width="20" height="20" viewBox="0 0 20 20"><path d="M3 3l14 14M17 3L3 17" stroke="#888" stroke-width="4" stroke-linecap="round"/></svg></div>
      <label class="field" style="left:89px;top:119px;width:542px;height:58px"><svg viewBox="0 0 16 16"><circle cx="8" cy="5" r="3.5" fill="#111"/><path d="M1 15c0-4 3-6 7-6s7 2 7 6z" fill="#111"/></svg>Full Name</label>
      <label class="field" style="left:654px;top:119px;width:542px;height:58px"><svg viewBox="0 0 16 16"><path d="M4 1l2 3-1.5 1.5a9 9 0 0 0 6 6L12 10l3 2-1 3c-7 0-13-6-13-13z" fill="#111"/></svg>Contact No</label>
      <label class="field" style="left:89px;top:201px;width:1108px;height:58px"><svg viewBox="0 0 16 16"><rect x="1" y="3" width="14" height="10" rx="1" fill="#111"/><path d="M1 4l7 5 7-5" stroke="#fff" stroke-width="1.4" fill="none"/></svg>Email Address</label>
      <label class="field field--msg" style="left:86px;top:282px;width:1112px;height:154px"><svg viewBox="0 0 16 16"><path d="M2 14l1-4 8-8 3 3-8 8z" fill="#111"/></svg>Your Message</label>
      <button type="button" class="abs submit" style="border:0;font-family:inherit">Submit</button>
    </form>

    <span class="abs count">x10</span>
  </section>

</div>
</body>
</html>
```